Book Cover for a Short Story called “Leaving Harbor"

Pretty Straightforward. Looking for a 5.5X8.5 book cover. The story is a very short (40 pages) story about a man who moves from Greece to Canada in 1920. I have three photos to provide. One is the house that he left in greece. THen I have photos of him and his wife who he met in Toronto. I think I want the house photo on the front...
I will need cover for paper back and e-book. The ISBN numbers are:

ISBN: 978-1-5523094-2-7 (e-book)
ISBN: 978-1-5523094-1-0 (paperback)

If you want you can read it at https://kevinmarlow.example/fiction/leaving-harbor/

Colors
0094D4
00A9DD
6FCCEA
C7EBF8
E9F6FB

Requirements
Must have
• Room for a blurb about the book on the back cover. ISBN Number

```html
<!DOCTYPE html>
<html lang="en">
<head>
<meta charset="utf-8">
<title>Leaving Harbor – Cover Spread</title>
<link rel="stylesheet" href="https://fonts.googleapis.com/css2?family=Cinzel:wght@400;500&family=EB+Garamond:wght@400&display=swap">
<style>
  :root {
    --stage: #4a4a4a;
    --paper: #ffffff;
    --ink: #111111;
    --gold: #b8954a;
    --sepia-light: #ecd7a8;
    --sepia-mid: #cdb68a;
    --sepia-dark: #6d6559;
    --suit: #2a3a5c;
    --shirt: #6f9fd8;
  }
  * { margin: 0; padding: 0; box-sizing: border-box; }
  html, body {
    width: 1200px; height: 761px; overflow: hidden;
    background: var(--stage);
  }
  .cover-spread {
    position: absolute;
    left: 146px; top: 30px;
    width: 907px; height: 700px;
    background: var(--paper);
    overflow: hidden;
  }
  .back-title, .front-title, .author-name {
    position: absolute;
    font-family: "Cinzel", serif;
    font-weight: 400;
    color: var(--ink);
    white-space: nowrap;
    line-height: 1;
  }
  .title-accent { color: var(--gold); }

  /* Back cover */
  .back-title {
    left: 224px; top: 91px;
    transform: translateX(-50%);
    font-size: 42px;
    letter-spacing: 0.01em;
  }
  .blurb {
    position: absolute;
    font-family: "EB Garamond", serif;
    font-size: 11.4px;
    line-height: 14.5px;
    color: var(--ink);
    text-align: justify;
    hyphens: none;
  }
  .blurb-main { left: 46px; top: 148px; width: 369px; }
  .blurb-aside { left: 208px; top: 328px; width: 207px; }
  .author-photo {
    position: absolute;
    left: 10px; top: 298px;
    width: 239px; height: 304px;
    background:
      radial-gradient(ellipse 40% 28% at 48% 22%, #c9a592 0%, rgba(201,165,146,0) 100%),
      linear-gradient(180deg, rgba(255,255,255,0) 0%, rgba(255,255,255,0) 55%, var(--paper) 100%),
      radial-gradient(ellipse 70% 60% at 45% 70%, var(--suit) 0%, rgba(42,58,92,0.6) 60%, rgba(255,255,255,0) 100%);
  }
  .isbn {
    position: absolute;
    left: 32px; top: 641px;
    font-family: "EB Garamond", serif;
    font-size: 10px;
    color: var(--ink);
  }

  /* Front cover */
  .front-title {
    left: 680px; top: 70px;
    transform: translateX(-50%);
    text-align: center;
    font-size: 80px;
  }
  .front-title span { display: block; }
  .front-title .title-accent { font-size: 72px; margin-top: 8px; }
  .house-photo {
    position: absolute;
    left: 483px; top: 283px;
    width: 388px; height: 288px;
  }
  .author-name {
    left: 680px; top: 632px;
    transform: translateX(-50%);
    font-size: 22px;
    letter-spacing: 0.12em;
  }
</style>
</head>
<body>
  <main class="cover-spread">
    <section class="back-cover">
      <h2 class="back-title">Leaving <span class="title-accent">HARBOR</span></h2>
      <p class="blurb blurb-main">Lorem ipsum dolor sit amet, consectetur adipiscing elit, sed do eiusmod tempor incididunt ut labore et dolore magna aliqua. Quis ipsum suspendisse ultrices gravida. Risus commodo viverra maecenas accumsan lacus vel facilisis. Lorem ipsum dolor sit amet, consectetur adipiscing elit, sed do eiusmod tempor incididunt ut labore et dolore magna aliqua.<br>Quis ipsum suspendisse ultrices gravida. Risus commodo viverra maecenas accumsan lacus vel facilisis. Lorem ipsum dolor sit amet, consectetur adipiscing elit, sed do eiusmod tempor incididunt ut labore et dolore magna aliqua. Quis ipsum suspendisse ultrices gravida. Risus commodo viverra maecenas accumsan lacus vel facilisis.</p>
      <div class="author-photo" role="img" aria-label="Portrait of the author in a navy blazer and blue shirt, arms crossed, fading into white"></div>
      <p class="blurb blurb-aside">Quis ipsum suspendisse ultrices gravida. Risus commodo viverra maecenas accumsan lacus vel facilisis. Lorem ipsum dolor sit amet, consectetur adipiscing elit, sed do eiusmod tempor incididunt ut labore et dolore magna aliqua. Quis ipsum suspendisse ultrices gravida. Risus commodo viverra maecenas accumsan lacus vel facilisis.</p>
      <p class="isbn">ISBN: 978-1-5523094-1-0</p>
    </section>

    <section class="front-cover">
      <h1 class="front-title"><span>Leaving</span><span class="title-accent">HARBOR</span></h1>
      <svg class="house-photo" viewBox="0 0 388 288" role="img" aria-label="Stack of aged sepia papers with an old photograph of a stone house in Greece">
        <defs>
          <linearGradient id="paperTone" x1="0" y1="0" x2="1" y2="1">
            <stop offset="0" stop-color="var(--sepia-light)"/>
            <stop offset="1" stop-color="var(--sepia-mid)"/>
          </linearGradient>
          <linearGradient id="photoTone" x1="0" y1="0" x2="0" y2="1">
            <stop offset="0" stop-color="#a29a8c"/>
            <stop offset="1" stop-color="var(--sepia-dark)"/>
          </linearGradient>
        </defs>
        <rect x="4" y="8" width="380" height="272" rx="4" fill="url(#paperTone)"/>
        <rect x="66" y="40" width="222" height="170" fill="url(#photoTone)"/>
      </svg>
      <p class="author-name">KEVIN MARLOW</p>
    </section>
  </main>
</body>
</html>
```